Wealth Education Business Needs Sharp Business Card Design

We need a business card design for a recently launched investor education business called Harbor Crest.

The final design should promote security, empowerment, self improvement and financial gain. The card will ideally promote the stature of the business.

For more information and colours please visit harborcrest.com.au

Target Market(s)

Corporate executives and high net worth individuals

Industry/Entity Type

Education

Contact Information for Business Card

```html
<!DOCTYPE html>
<html lang="en">
<head>
<meta charset="utf-8">
<title>Harbor Crest – Business Card</title>
<link rel="stylesheet" href="https://fonts.googleapis.com/css2?family=Oswald:wght@500;600&family=Open+Sans:wght@400;600;700&display=swap">
<style>
  :root {
    --navy: #1c2a3e;
    --white: #ffffff;
    --teal: #1f8a8c;
    --grey-text: #9aa3ad;
    --brand-grey: #a9b0b8;
    --ink: #2a2f36;
    --rule: #cfd3d8;
    --page: #e9e7e3;
  }
  * { margin: 0; padding: 0; box-sizing: border-box; }
  html, body { width: 1200px; height: 902px; overflow: hidden; }
  body {
    background: var(--page);
    font-family: "Open Sans", Arial, sans-serif;
    position: relative;
  }
  .card {
    position: absolute;
    top: 301px;
    width: 520px;
    height: 300px;
    border-radius: 16px;
    overflow: hidden;
    background: var(--navy);
    box-shadow: 0 6px 18px rgba(0,0,0,0.18);
  }
  .card--front { left: 50px; }
  .card--back { left: 630px; }

  /* Front */
  .front-brand {
    position: absolute;
    left: 0; right: 0; top: 96px;
    display: flex; align-items: center; justify-content: center; gap: 14px;
  }
  .brand-dot {
    width: 34px; height: 34px; border-radius: 50%;
    background: var(--teal);
  }
  .brand-name {
    font-family: "Oswald", Arial, sans-serif;
    font-weight: 600;
    font-size: 40px;
    letter-spacing: 2px;
    color: var(--white);
    text-transform: uppercase;
    line-height: 1;
  }
  .front-tagline {
    position: absolute; left: 0; right: 0; top: 150px;
    text-align: center;
    font-family: "Oswald", Arial, sans-serif;
    font-weight: 500;
    font-size: 14px;
    letter-spacing: 5px;
    color: var(--teal);
    text-transform: uppercase;
  }
  .front-web {
    position: absolute; left: 0; right: 0; bottom: 54px;
    text-align: center;
    font-size: 13px;
    color: var(--grey-text);
    letter-spacing: 0.5px;
  }

  /* Back */
  .back-band { position: absolute; inset: 0; }
  .back-brand {
    position: absolute; left: 40px; top: 28px;
    display: flex; align-items: center; gap: 10px;
  }
  .back-brand .brand-name { font-size: 30px; color: var(--brand-grey); }
  .back-brand .brand-dot { width: 24px; height: 24px; }
  .person {
    position: absolute; left: 40px; top: 150px;
  }
  .person-name {
    font-weight: 700; font-size: 20px; color: var(--teal);
    text-transform: uppercase; letter-spacing: 0.3px;
  }
  .person-name span { color: var(--ink); }
  .person-title { font-size: 13px; color: var(--ink); margin-top: 2px; margin-left: 74px; }
  .contacts {
    position: absolute; left: 262px; top: 104px;
    border-left: 1px solid var(--rule);
    padding-left: 14px;
    list-style: none;
    font-size: 12.5px; color: var(--ink); line-height: 1.55;
  }
  .contacts li { display: flex; gap: 8px; align-items: flex-start; }
  .contacts svg { width: 11px; height: 11px; margin-top: 4px; flex: none; fill: var(--ink); color: var(--ink); }
  .back-web {
    position: absolute; right: 34px; bottom: 20px;
    font-size: 17px; color: var(--white); letter-spacing: 0.3px;
  }
</style>
</head>
<body>
  <section class="card card--front" aria-label="Card front">
    <div class="front-brand">
      <span class="brand-dot"></span>
      <span class="brand-name">Harbor Crest</span>
    </div>
    <p class="front-tagline">Study Build Thrive</p>
    <p class="front-web">www.harborcrest.com.au</p>
  </section>

  <section class="card card--back" aria-label="Card back">
    <svg class="back-band" viewBox="0 0 520 300" preserveAspectRatio="none" aria-hidden="true">
      <path d="M0 112 C150 92 330 70 520 30 L520 222 C350 232 170 250 0 276 Z" fill="var(--white)"/>
    </svg>
    <div class="back-brand">
      <span class="brand-dot"></span>
      <span class="brand-name">Harbor Crest</span>
    </div>
    <div class="person">
      <p class="person-name">Your <span>Name</span></p>
      <p class="person-title">Title</p>
    </div>
    <ul class="contacts">
      <li><svg viewBox="0 0 12 12"><path d="M2 1l2 0 1 3-1.3 1a7 7 0 0 0 3.3 3.3L8 7l3 1v2c0 .6-.5 1-1 1A9 9 0 0 1 1 2c0-.5.4-1 1-1z"/></svg>1300 555 017</li>
      <li><svg viewBox="0 0 12 12"><rect x="1" y="1" width="10" height="10" rx="1" fill="none" stroke="currentColor"/><rect x="3" y="3" width="6" height="3"/></svg>+613 9555 2740</li>
      <li><svg viewBox="0 0 12 12"><rect x="0.5" y="2" width="11" height="8"/><path d="M1 2.5l5 4 5-4" stroke="#fff" fill="none"/></svg>hello@harborcrest.com.au</li>
      <li><svg viewBox="0 0 12 12"><path d="M6 0a4 4 0 0 0-4 4c0 3 4 8 4 8s4-5 4-8a4 4 0 0 0-4-4zm0 5.5A1.5 1.5 0 1 1 6 2.5a1.5 1.5 0 0 1 0 3z"/></svg><span>Level 2, 48 Quayside Walk<br>Southbank VIC 3006</span></li>
    </ul>
    <p class="back-web">www.harborcrest.com.au</p>
  </section>
</body>
</html>
```